you will use Ai to Copy the website Brivanta.com to come up with the basic frame work and it will give you the understanding of how I would like Kelbrava.com to be like. Kelbrava.com is a peer to peer rv rental site very similar to both of the other rv rental sites the difference is that are commission based 20% and above per rental and we will be one flat monthly rate and they keep all the earnings. Below is photo that will help you with the color scheme and the look and feel of the design

1 page

```html
<!DOCTYPE html>
<html lang="en">
<head>
<meta charset="utf-8">
<title>Kelbrava.com — Rent An RV</title>
<link rel="stylesheet" href="https://fonts.googleapis.com/css2?family=DM+Serif+Display&family=Plus+Jakarta+Sans:wght@400;500;600;700&display=swap">
<style>
:root{
  --lime:#8dc63f;
  --lime-dark:#6fa52a;
  --ink:#1c1f1d;
  --muted:#6b716d;
  --line:#e1e4df;
  --tile:#eef1ea;
  --page:#ffffff;
  --soft:#f5f6f3;
  --footer:#16261d;
  --white:#ffffff;
}
*{box-sizing:border-box;margin:0;padding:0}
html,body{width:1200px;height:3617px;overflow:hidden}
body{position:relative;background:var(--page);font-family:"Plus Jakarta Sans",Arial,sans-serif;color:var(--ink)}
.serif{font-family:"DM Serif Display",Georgia,serif;font-weight:400}
.abs{position:absolute}
.btn-pill{display:inline-flex;align-items:center;justify-content:center;border-radius:999px;background:var(--white);color:var(--ink);font-weight:600;font-size:14px}

/* hero */
.hero-photo{left:0;top:0;width:1200px;height:502px;background:linear-gradient(180deg,#3a4550 0%,#4b5b66 35%,#2e4150 60%,#1e2a2e 100%)}
.hero-photo::after{content:"";position:absolute;right:150px;top:120px;width:380px;height:300px;border-radius:40px 30px 10px 10px;background:linear-gradient(160deg,#d7dadb,#9ca3a7);opacity:.35}
.logo{left:36px;top:22px;display:flex;align-items:center;gap:10px;color:var(--white);font-weight:700;font-size:24px}
.logo-mark{width:14px;height:14px;border-radius:50%;background:var(--lime)}
.mode-toggle{left:480px;top:28px;width:222px;height:40px;border-radius:999px;background:rgba(255,255,255,.25);display:flex;align-items:center;padding:4px;gap:4px}
.mode-toggle span{flex:1;height:32px;border-radius:999px;display:flex;align-items:center;justify-content:center;font-size:13px;color:var(--white);font-weight:500}
.mode-toggle .on{background:var(--white);color:var(--ink)}
.host-btn{left:964px;top:27px;width:157px;height:41px;border-radius:999px;background:var(--lime);color:var(--ink);font-size:13px;font-weight:600;display:flex;align-items:center;justify-content:center}
.user-btn{left:1134px;top:30px;width:36px;height:36px;border-radius:50%;border:1.5px solid rgba(255,255,255,.8);display:flex;align-items:center;justify-content:center}
.hero-kicker{left:30px;top:298px;color:var(--lime);font-size:11px;font-weight:600;letter-spacing:.3px}
.hero-title{left:30px;top:318px;width:680px;color:var(--white);font-size:38px;line-height:49px}

/* search */
.search{left:30px;top:438px;width:1142px;height:152px;background:var(--white);border-radius:12px;box-shadow:0 10px 30px rgba(0,0,0,.10);padding:11px 12px}
.type-tabs{display:flex;gap:8px;font-size:13px;font-weight:500}
.type-tabs span{padding:0 15px;height:35px;display:flex;align-items:center;border-radius:4px}
.type-tabs .on{background:var(--lime);color:var(--ink);padding:0 26px}
.fields{position:absolute;left:12px;top:64px;width:1118px;height:75px;border:1px solid var(--line);display:flex}
.field{border-right:1px solid var(--line);padding:18px 30px;display:flex;flex-direction:column;gap:6px}
.field small{font-size:10px;color:var(--muted)}
.field b{font-size:14px;font-weight:600}
.field.f1{width:202px}.field.f2{width:285px;align-items:center}.field.f3{width:277px;align-items:center}.field.f4{width:270px;align-items:center;border-right:0}
.search-go{position:absolute;right:-1px;top:-1px;width:85px;height:75px;background:var(--lime);display:flex;align-items:center;justify-content:center;border-radius:0 4px 4px 0}

/* promo */
.promo{width:561px;height:294px;border-radius:8px;overflow:hidden;color:var(--white)}
.promo .photo{position:absolute;inset:0}
.promo .text{position:absolute;left:18px;top:140px;width:430px}
.promo h3{font-size:28px;line-height:36px}
.promo p{font-size:12.5px;line-height:20px;margin-top:8px}
.promo .btn-pill{margin-top:18px;height:36px;padding:0 22px;font-size:13px}

/* section heads */
.sec-title{left:30px;font-size:36px;line-height:44px}
.sec-sub{left:30px;font-size:13px;color:var(--muted)}
.arrows{display:flex;gap:21px}
.arrow{width:32px;height:32px;border-radius:50%;background:#bfc3c0;display:flex;align-items:center;justify-content:center}
.filters{left:30px;top:1085px;display:flex;align-items:center;gap:28px;font-size:13px;color:var(--muted)}
.filters .on{background:var(--lime);color:var(--ink);font-weight:600;height:34px;padding:0 22px;border-radius:4px;display:flex;align-items:center;gap:6px}
.filters span{display:flex;align-items:center;gap:6px}

/* rental cards */
.rv{width:266px;height:318px;border:1px solid var(--line);border-radius:8px;overflow:hidden;background:var(--white)}
.rv .photo{height:186px;position:relative}
.rating{position:absolute;left:17px;top:10px;background:var(--white);border-radius:999px;font-size:10px;font-weight:600;padding:3px 8px;display:flex;gap:3px;align-items:center}
.rating i{color:#f5a623;font-style:normal}
.fav{position:absolute;right:8px;top:8px;width:22px;height:22px;border-radius:50%;background:rgba(255,255,255,.9);display:flex;align-items:center;justify-content:center}
.dots{position:absolute;left:50%;bottom:8px;transform:translateX(-50%);display:flex;gap:3px}
.dots b{width:4px;height:4px;border-radius:50%;background:rgba(255,255,255,.8)}
.rv .info{padding:12px 18px}
.rv h4{font-size:13px;font-weight:600}
.rv .meta{font-size:11.5px;color:var(--muted);margin-top:8px}
.rv .loc{font-size:11.5px;color:var(--muted);margin-top:6px}
.rv .price{font-size:18px;font-weight:600;margin-top:12px}
.view-all{left:518px;top:1830px;width:164px;height:42px;border:1px solid #9aa09c;border-radius:999px;display:flex;align-items:center;justify-content:center;font-size:13px;font-weight:600}

/* parks */
.park{width:363px;height:400px;border-radius:8px;overflow:hidden;color:var(--white)}
.park .photo{position:absolute;inset:0}
.state{position:absolute;left:18px;top:18px;background:rgba(20,30,30,.55);border-radius:999px;font-size:9px;font-weight:600;padding:6px 12px 6px 24px}
.state svg{position:absolute;left:10px;top:6px}
.park h3{position:absolute;left:18px;top:196px;font-size:36px}
.park .btn-pill{position:absolute;left:18px;top:266px;height:33px;padding:0 22px;font-size:13px}
.thumbs{position:absolute;left:18px;top:313px;display:flex;gap:10px}
.thumbs div{width:74px;height:67px;border-radius:4px;background:linear-gradient(180deg,#b9c7d2,#8a8f8c)}
.thumbs .more{background:rgba(255,255,255,.88);color:var(--ink);display:flex;flex-direction:column;align-items:center;justify-content:center;font-size:13px;font-weight:600}
.thumbs .more small{font-size:10px;font-weight:400;color:var(--muted);margin-top:4px}

/* destinations */
.state-select{left:1009px;top:2537px;width:163px;height:43px;border:1px solid #9aa09c;border-radius:4px;display:flex;align-items:center;justify-content:center;gap:10px;font-size:13px;font-weight:500}
.dest{width:150px;height:58px;border-radius:4px;background:var(--tile);padding:12px 12px}
.dest b{display:block;font-size:13px;font-weight:600}
.dest small{display:block;font-size:8px;color:var(--muted);margin-top:5px}
.dest.on{background:var(--lime)}

/* footer */
.footer{left:0;top:3284px;width:1200px;height:333px;background:var(--footer);color:var(--white)}
.footer .brand{left:70px;top:70px;display:flex;align-items:center;gap:12px;font-size:40px;font-weight:700}
.footer .brand i{width:18px;height:18px;border-radius:50%;background:var(--lime)}
.footer .about{left:60px;top:154px;width:300px;font-size:10.5px;line-height:17px;text-align:center;color:#cfd6d1}
.fcol h5{font-size:17px;margin-bottom:14px}
.fcol a{display:block;color:#d4dad6;font-size:12px;text-decoration:none;margin-bottom:13px}
.contact a{display:flex;align-items:center;gap:10px}
.socials{display:flex;gap:13px}
.socials span{width:42px;height:42px;border-radius:50%;border:1.5px solid #d4dad6;display:flex;align-items:center;justify-content:center}
.socials span i{width:10px;height:10px;border-radius:2px;background:#d4dad6}
.copy{left:30px;top:292px;font-size:11.5px;color:#d4dad6}
.legal{right:60px;top:292px;display:flex;gap:20px;font-size:11.5px;color:#d4dad6}
</style>
</head>
<body>

<!-- hero -->
<div class="abs hero-photo" role="img" aria-label="White camper van parked beside a lake with mountains under a stormy sky"></div>
<div class="abs logo"><span class="logo-mark"></span>Kelbrava.com</div>
<div class="abs mode-toggle"><span class="on">Rent an RV</span><span>List your RV</span></div>
<div class="abs host-btn">Become a Host</div>
<div class="abs user-btn"><svg width="16" height="16" viewBox="0 0 16 16" fill="none" stroke="#fff" stroke-width="1.4"><circle cx="8" cy="5" r="3"/><path d="M2.5 14c.8-3 3-4.2 5.5-4.2s4.7 1.2 5.5 4.2"/></svg></div>
<div class="abs hero-kicker">NO COMMISSION FEES FOR HOSTS</div>
<h1 class="abs hero-title serif">Rent An RV. Make Memories. Keep The Adventure Going.</h1>

<!-- search -->
<div class="abs search">
  <div class="type-tabs"><span class="on">All Types</span><span>Drivable</span><span>Towable</span><span>Deliverable</span></div>
  <div class="fields">
    <div class="field f1"><small>Choose</small><b>Location</b></div>
    <div class="field f2"><small>Dates</small><b>Any Dates</b></div>
    <div class="field f3"><small>Guests</small><b>2 Guests</b></div>
    <div class="field f4"><small>Driver's Age</small><b>25+</b></div>
    <div class="search-go"><svg width="22" height="22" viewBox="0 0 22 22" fill="none" stroke="#1c1f1d" stroke-width="2"><circle cx="9.5" cy="9.5" r="6.5"/><path d="M14.5 14.5l5 5"/></svg></div>
  </div>
</div>

<!-- promos -->
<div class="abs promo" style="left:30px;top:615px">
  <div class="photo" role="img" aria-label="Row of white motorhomes parked side by side" style="background:linear-gradient(180deg,#9aa3a6 0%,#6b7478 55%,#2c3336 100%)"></div>
  <div class="text"><h3 class="serif">Get It Delivered</h3><p>Love Camping, But Don't Love Driving? Get An RV Delivered And Set Up At A Location Of Your Choice.</p><span class="btn-pill">Get It Delivered</span></div>
</div>
<div class="abs promo" style="left:608px;top:615px">
  <div class="photo" role="img" aria-label="Camper van driving a coastal road beside the sea" style="background:linear-gradient(180deg,#3d5a45 0%,#476b78 45%,#2f4438 100%)"></div>
  <div class="text"><h3 class="serif">Pick It Up &amp; Hit The Road</h3><p>Get Ready For The Ultimate Road Trip. Pick Up An RV Near You, Or At A Destination Of Your Choice.</p><span class="btn-pill">Pick It Up</span></div>
</div>

<!-- best rentals -->
<h2 class="abs sec-title serif" style="top:982px">Find The Best RV Rentals In The Country</h2>
<p class="abs sec-sub" style="top:1038px">Explore The Open Road In The Perfect RV Rental. Or, Get One Delivered And Set Up For You.</p>
<div class="abs filters">
  <span class="on"><svg width="12" height="12" viewBox="0 0 12 12" fill="none" stroke="#1c1f1d" stroke-width="1.3"><path d="M6 10.5S1.5 7.8 1.5 4.6A2.3 2.3 0 016 3.4a2.3 2.3 0 014.5 1.2C10.5 7.8 6 10.5 6 10.5z"/></svg>Popular</span>
  <span>Camper Van</span><span>Pets</span><span>Vintage</span><span>Value</span><span>Small Trailer</span>
</div>
<div class="abs arrows" style="left:1081px;top:1083px">
  <span class="arrow"><svg width="14" height="14" viewBox="0 0 14 14" fill="none" stroke="#fff" stroke-width="1.8"><path d="M12 7H2M6 3L2 7l4 4"/></svg></span>
  <span class="arrow"><svg width="14" height="14" viewBox="0 0 14 14" fill="none" stroke="#fff" stroke-width="1.8"><path d="M2 7h10M8 3l4 4-4 4"/></svg></span>
</div>

<div class="abs rv" style="left:30px;top:1145px"><div class="photo" role="img" aria-label="Motorhome parked under a dramatic evening sky" style="background:linear-gradient(180deg,#7b6d8a,#b8a9b0 50%,#7d8a66)"><span class="rating"><i>★</i>4.9</span><span class="fav"><svg width="12" height="12" viewBox="0 0 12 12" fill="#e53935"><path d="M6 10.5S1.5 7.8 1.5 4.6A2.3 2.3 0 016 3.4a2.3 2.3 0 014.5 1.2C10.5 7.8 6 10.5 6 10.5z"/></svg></span><span class="dots"><b></b><b></b><b></b><b></b><b></b></span></div><div class="info"><h4>Mori Van CA</h4><p class="meta">Camper Van &nbsp;•&nbsp; Sleeps 2 &nbsp;•&nbsp; 16ft</p><p class="loc">San Diego, CA</p><p class="price">$150/ Night</p></div></div>
<div class="abs rv" style="left:321px;top:1145px"><div class="photo" role="img" aria-label="Black and white motorhome on a gravel lot" style="background:linear-gradient(180deg,#8fb0d0,#c9c6bd 55%,#8c8a7d)"><span class="rating"><i>★</i>4.9</span><span class="fav"><svg width="12" height="12" viewBox="0 0 12 12" fill="none" stroke="#777" stroke-width="1.1"><path d="M6 10.5S1.5 7.8 1.5 4.6A2.3 2.3 0 016 3.4a2.3 2.3 0 014.5 1.2C10.5 7.8 6 10.5 6 10.5z"/></svg></span><span class="dots"><b></b><b></b><b></b><b></b><b></b></span></div><div class="info"><h4>Mori Van CA</h4><p class="meta">Camper Van &nbsp;•&nbsp; Sleeps 2 &nbsp;•&nbsp; 16ft</p><p class="loc">San Diego, CA</p><p class="price">$150/ Night</p></div></div>
<div class="abs rv" style="left:615px;top:1145px"><div class="photo" role="img" aria-label="Motorhome beside autumn trees and mountains" style="background:linear-gradient(180deg,#5b89c4,#c9a34a 45%,#7f8f6a)"><span class="rating"><i>★</i>4.9</span><span class="fav"><svg width="12" height="12" viewBox="0 0 12 12" fill="none" stroke="#777" stroke-width="1.1"><path d="M6 10.5S1.5 7.8 1.5 4.6A2.3 2.3 0 016 3.4a2.3 2.3 0 014.5 1.2C10.5 7.8 6 10.5 6 10.5z"/></svg></span><span class="dots"><b></b><b></b><b></b><b></b><b></b></span></div><div class="info"><h4>Mori Van CA</h4><p class="meta">Camper Van &nbsp;•&nbsp; Sleeps 2 &nbsp;•&nbsp; 16ft</p><p class="loc">San Diego, CA</p><p class="price">$150/ Night</p></div></div>
<div class="abs rv" style="left:907px;top:1145px"><div class="photo" role="img" aria-label="Camper van parked in a pine forest" style="background:linear-gradient(180deg,#6e7f3e,#a4925e 50%,#5c5a3c)"><span class="rating"><i>★</i>4.9</span><span class="fav"><svg width="12" height="12" viewBox="0 0 12 12" fill="none" stroke="#777" stroke-width="1.1"><path d="M6 10.5S1.5 7.8 1.5 4.6A2.3 2.3 0 016 3.4a2.3 2.3 0 014.5 1.2C10.5 7.8 6 10.5 6 10.5z"/></svg></span><span class="dots"><b></b><b></b><b></b><b></b><b></b></span></div><div class="info"><h4>Mori Van CA</h4><p class="meta">Camper Van &nbsp;•&nbsp; Sleeps 2 &nbsp;•&nbsp; 16ft</p><p class="loc">San Diego, CA</p><p class="price">$150/ Night</p></div></div>

<div class="abs rv" style="left:30px;top:1488px"><div class="photo" role="img" aria-label="White motorhome with awning beside trees" style="background:linear-gradient(180deg,#7e9aa8,#c5cbc4 50%,#6f7d63)"><span class="rating"><i>★</i>4.9</span><span class="fav"><svg width="12" height="12" viewBox="0 0 12 12" fill="none" stroke="#777" stroke-width="1.1"><path d="M6 10.5S1.5 7.8 1.5 4.6A2.3 2.3 0 016 3.4a2.3 2.3 0 014.5 1.2C10.5 7.8 6 10.5 6 10.5z"/></svg></span><span class="dots"><b></b><b></b><b></b><b></b><b></b></span></div><div class="info"><h4>Mori Van CA</h4><p class="meta">Camper Van &nbsp;•&nbsp; Sleeps 2 &nbsp;•&nbsp; 16ft</p><p class="loc">San Diego, CA</p><p class="price">$150/ Night</p></div></div>
<div class="abs rv" style="left:321px;top:1488px"><div class="photo" role="img" aria-label="Motorhome parked on grass under blue sky" style="background:linear-gradient(180deg,#6ea0d8,#d7dbd6 50%,#6f8c4a)"><span class="rating"><i>★</i>4.9</span><span class="fav"><svg width="12" height="12" viewBox="0 0 12 12" fill="none" stroke="#777" stroke-width="1.1"><path d="M6 10.5S1.5 7.8 1.5 4.6A2.3 2.3 0 016 3.4a2.3 2.3 0 014.5 1.2C10.5 7.8 6 10.5 6 10.5z"/></svg></span><span class="dots"><b></b><b></b><b></b><b></b><b></b></span></div><div class="info"><h4>Mori Van CA</h4><p class="meta">Camper Van &nbsp;•&nbsp; Sleeps 2 &nbsp;•&nbsp; 16ft</p><p class="loc">San Diego, CA</p><p class="price">$150/ Night</p></div></div>
<div class="abs rv" style="left:615px;top:1488px"><div class="photo" role="img" aria-label="Motorhome on a road under a pale sky" style="background:linear-gradient(180deg,#9ab7d3,#d3d6d4 55%,#7d8273)"><span class="rating"><i>★</i>4.9</span><span class="fav"><svg width="12" height="12" viewBox="0 0 12 12" fill="none" stroke="#777" stroke-width="1.1"><path d="M6 10.5S1.5 7.8 1.5 4.6A2.3 2.3 0 016 3.4a2.3 2.3 0 014.5 1.2C10.5 7.8 6 10.5 6 10.5z"/></svg></span><span class="dots"><b></b><b></b><b></b><b></b><b></b></span></div><div class="info"><h4>Mori Van CA</h4><p class="meta">Camper Van &nbsp;•&nbsp; Sleeps 2 &nbsp;•&nbsp; 16ft</p><p class="loc">San Diego, CA</p><p class="price">$150/ Night</p></div></div>
<div class="abs rv" style="left:907px;top:1488px"><div class="photo" role="img" aria-label="Motorhome parked on a sandy lot" style="background:linear-gradient(180deg,#8fb4d6,#d8d4c8 55%,#a39b86)"><span class="rating"><i>★</i>4.9</span><span class="fav"><svg width="12" height="12" viewBox="0 0 12 12" fill="none" stroke="#777" stroke-width="1.1"><path d="M6 10.5S1.5 7.8 1.5 4.6A2.3 2.3 0 016 3.4a2.3 2.3 0 014.5 1.2C10.5 7.8 6 10.5 6 10.5z"/></svg></span><span class="dots"><b></b><b></b><b></b><b></b><b></b></span></div><div class="info"><h4>Mori Van CA</h4><p class="meta">Camper Van &nbsp;•&nbsp; Sleeps 2 &nbsp;•&nbsp; 16ft</p><p class="loc">San Diego, CA</p><p class="price">$150/ Night</p></div></div>

<a class="abs view-all" style="color:var(--ink);text-decoration:none">View All Rentals</a>

<!-- national parks -->
<h2 class="abs sec-title serif" style="top:1946px">Explore Rentals Near National Parks</h2>
<p class="abs sec-sub" style="top:2000px">Explore The Open Road In The Perfect RV Rental. Or, Get One Delivered And Set Up For You.</p>
<div class="abs arrows" style="left:1083px;top:1967px">
  <span class="arrow"><svg width="14" height="14" viewBox="0 0 14 14" fill="none" stroke="#fff" stroke-width="1.8"><path d="M12 7H2M6 3L2 7l4 4"/></svg></span>
  <span class="arrow"><svg width="14" height="14" viewBox="0 0 14 14" fill="none" stroke="#fff" stroke-width="1.8"><path d="M2 7h10M8 3l4 4-4 4"/></svg></span>
</div>

<div class="abs park" style="left:30px;top:2049px">
  <div class="photo" role="img" aria-label="Geyser erupting under a blue sky with clouds" style="background:linear-gradient(180deg,#3f7bc2 0%,#b9c9d8 40%,#7f8a86 75%,#222826 100%)"></div>
  <span class="state"><svg width="8" height="10" viewBox="0 0 8 10" fill="#fff"><path d="M4 0a3.5 3.5 0 013.5 3.5C7.5 6 4 10 4 10S.5 6 .5 3.5A3.5 3.5 0 014 0zm0 2a1.5 1.5 0 100 3 1.5 1.5 0 000-3z"/></svg>WYOMING</span>
  <h3 class="serif">Yellowstone</h3><span class="btn-pill">Book Now</span>
  <div class="thumbs"><div role="img" aria-label="RV thumbnail"></div><div role="img" aria-label="RV thumbnail"></div><div role="img" aria-label="RV thumbnail"></div><div class="more">+283<small>Rentals</small></div></div>
</div>
<div class="abs park" style="left:418px;top:2049px">
  <div class="photo" role="img" aria-label="Red sandstone canyon walls under a blue sky" style="background:linear-gradient(180deg,#2e6fc1 0%,#c8632e 35%,#d98a4a 60%,#2b1f1a 100%)"></div>
  <span class="state"><svg width="8" height="10" viewBox="0 0 8 10" fill="#fff"><path d="M4 0a3.5 3.5 0 013.5 3.5C7.5 6 4 10 4 10S.5 6 .5 3.5A3.5 3.5 0 014 0zm0 2a1.5 1.5 0 100 3 1.5 1.5 0 000-3z"/></svg>UTAH</span>
  <h3 class="serif">Zion</h3><span class="btn-pill">Book Now</span>
  <div class="thumbs"><div role="img" aria-label="RV thumbnail"></div><div role="img" aria-label="RV thumbnail"></div><div role="img" aria-label="RV thumbnail"></div><div class="more">+283<small>Rentals</small></div></div>
</div>
<div class="abs park" style="left:806px;top:2049px">
  <div class="photo" role="img" aria-label="Mountain peaks above a turquoise glacial lake" style="background:linear-gradient(180deg,#4b82c4 0%,#8a9aa6 35%,#3f6150 60%,#1f8a8a 75%,#17241f 100%)"></div>
  <span class="state"><svg width="8" height="10" viewBox="0 0 8 10" fill="#fff"><path d="M4 0a3.5 3.5 0 013.5 3.5C7.5 6 4 10 4 10S.5 6 .5 3.5A3.5 3.5 0 014 0zm0 2a1.5 1.5 0 100 3 1.5 1.5 0 000-3z"/></svg>MONTANA</span>
  <h3 class="serif">Glacier</h3><span class="btn-pill">Book Now</span>
  <div class="thumbs"><div role="img" aria-label="RV thumbnail"></div><div role="img" aria-label="RV thumbnail"></div><div role="img" aria-label="RV thumbnail"></div><div class="more">+283<small>Rentals</small></div></div>
</div>

<!-- destinations -->
<h2 class="abs sec-title serif" style="top:2522px">Popular RV Rental Destinations</h2>
<p class="abs sec-sub" style="top:2577px">Explore The Open Road In The Perfect RV Rental. Or, Get One Delivered And Set Up For You.</p>
<div class="abs state-select">Search By State <svg width="11" height="7" viewBox="0 0 11 7" fill="none" stroke="#1c1f1d" stroke-width="1.5"><path d="M1 1l4.5 4.5L10 1"/></svg></div>

<div class="abs dest" style="left:30px;top:2624px"><b>Atlanta, GA</b><small>751 RV Rentals</small></div>
<div class="abs dest on" style="left:194px;top:2624px"><b>Austin, TX</b><small>751 RV Rentals</small></div>
<div class="abs dest" style="left:359px;top:2624px"><b>Boston, MA</b><small>751 RV Rentals</small></div>
<div class="abs dest" style="left:523px;top:2624px"><b>Chicago, IL</b><small>751 RV Rentals</small></div>
<div class="abs dest" style="left:688px;top:2624px"><b>Maui, HI</b><small>751 RV Rentals</small></div>
<div class="abs dest" style="left:853px;top:2624px"><b>Minneapolis, MN</b><small>751 RV Rentals</small></div>
<div class="abs dest" style="left:1018px;top:2624px"><b>New York, NY</b><small>751 RV Rentals</small></div>

<div class="abs dest" style="left:30px;top:2707px"><b>Dallas, TX</b><small>751 RV Rentals</small></div>
<div class="abs dest" style="left:194px;top:2707px"><b>Houston, TX</b><small>751 RV Rentals</small></div>
<div class="abs dest" style="left:359px;top:2707px"><b>Kailua-Kona, HI</b><small>751 RV Rentals</small></div>
<div class="abs dest" style="left:523px;top:2707px"><b>Las Vegas, NV</b><small>751 RV Rentals</small></div>
<div class="abs dest" style="left:688px;top:2707px"><b>Miami, FL</b><small>751 RV Rentals</small></div>
<div class="abs dest" style="left:853px;top:2707px"><b>Nashville, TN</b><small>751 RV Rentals</small></div>
<div class="abs dest" style="left:1018px;top:2707px"><b>Orlando, FL</b><small>751 RV Rentals</small></div>

<div class="abs dest" style="left:30px;top:2789px"><b>Denver, CO</b><small>751 RV Rentals</small></div>
<div class="abs dest" style="left:194px;top:2789px"><b>Honolulu, HI</b><small>751 RV Rentals</small></div>
<div class="abs dest" style="left:359px;top:2789px"><b>Kauai, HI</b><small>751 RV Rentals</small></div>
<div class="abs dest" style="left:523px;top:2789px"><b>Los Angeles, CA</b><small>751 RV Rentals</small></div>

<!-- camping promos -->
<div class="abs promo" style="left:30px;top:2922px">
  <div class="photo" role="img" aria-label="Family relaxing by a campfire beside their RV in a forest" style="background:linear-gradient(180deg,#4d5a42 0%,#5e5a48 50%,#2b2a22 100%)"></div>
  <div class="text" style="top:130px"><h3 class="serif">Rent An RV And Camp In Our National Parks</h3><span class="btn-pill">Book Now</span></div>
</div>
<div class="abs promo" style="left:608px;top:2922px">
  <div class="photo" role="img" aria-label="Family enjoying a campsite next to their trailer" style="background:linear-gradient(180deg,#5c6b52 0%,#8a8576 45%,#4e5542 100%)"></div>
  <div class="text" style="top:130px"><h3 class="serif">Rent An RV And Camp In Our State Parks</h3><span class="btn-pill">Book Now</span></div>
</div>

<!-- footer -->
<footer class="abs footer">
  <div class="abs brand"><i></i>Kelbrava.com</div>
  <p class="abs about">Kelbrava Makes It Easier To Experience The Freedom Of RV Travel Without The Hassle Of Traditional RV Ownership. We Connect Travelers With RV Owners Across The Country.</p>
  <div class="abs fcol" style="left:539px;top:70px"><h5 class="serif">Quick Links</h5><a>Rent an RV</a><a>List your RV</a><a>Become a host</a><a>Get help</a></div>
  <div class="abs fcol contact" style="left:740px;top:70px"><h5 class="serif">Contact Us</h5>
    <a><svg width="14" height="14" viewBox="0 0 14 14" fill="#d4dad6"><path d="M3 1l2.5 3-1.3 1.5a8 8 0 004.3 4.3L10 8.5 13 11l-1.5 2C6 13 1 8 1 2.5z"/></svg>+123-456-789</a>
    <a><svg width="14" height="12" viewBox="0 0 14 12" fill="none" stroke="#d4dad6" stroke-width="1.3"><rect x="1" y="1.5" width="12" height="9" rx="1"/><path d="M1.5 2l5.5 4.5L12.5 2"/></svg>info@kelbrava.com</a>
    <a><svg width="12" height="15" viewBox="0 0 8 10" fill="#d4dad6"><path d="M4 0a3.5 3.5 0 013.5 3.5C7.5 6 4 10 4 10S.5 6 .5 3.5A3.5 3.5 0 014 0zm0 2a1.5 1.5 0 100 3 1.5 1.5 0 000-3z"/></svg>USA</a>
  </div>
  <div class="abs fcol" style="left:991px;top:70px"><h5 class="serif">Social links</h5>
    <div class="socials"><span aria-label="Social link"><i></i></span><span aria-label="Social link"><i></i></span><span aria-label="Social link"><i></i></span></div>
  </div>
  <p class="abs copy">© 2026 Kelbrava. All Rights Reserved.</p>
  <div class="abs legal"><span>Language &amp; Currency</span><span>Privacy Policy</span><span>Teams &amp; Conditions</span></div>
</footer>

</body>
</html>
```